Online homewares store needs a web design

We need a web design for a new high-end online homewares store. We are starting small with only 5 major categories.

Rugs
Bathe
Dine
Decorative
Sleep

This is just for design. No coding needed.

Please make high-end, sophisticated and minimal.

I have included some pictures to give you an idea of the products. I would like to showcase some of the pictures on the web page.

The website will be using an e-commerce function.

I have included the logo studio nine harbors.

I like this website
http://mapleandquarrylane.example/

or

borvanest.example.au

Simple but effective - not too busy

Project Deadline Extended
Reason: I would like to extend my deadline to give designers more time to do quality work - as requested!! Thanks.

Target Market(s)

Females in the age bracket of 25-45

Males who are very house proud 25-45

Industry/Entity Type

Store

Requirements
Must have
• Upmarket

```html
<!DOCTYPE html>
<html lang="en">
<head>
<meta charset="utf-8">
<title>studio nine harbors – homewares</title>
<link rel="stylesheet" href="https://fonts.googleapis.com/css2?family=Source+Sans+3:wght@300;400;600&display=swap">
<style>
:root{
  --ink:#222222;
  --ink-deep:#111111;
  --bar:#2b2b2b;
  --field:#3a3a3a;
  --pink:#ee2a6e;
  --sand:#edebe6;
  --white:#ffffff;
  --text:#333333;
  --rule:#e3e3e3;
  --yellow:#f4e66a;
}
*{box-sizing:border-box;margin:0;padding:0}
html,body{width:986px;height:1200px;overflow:hidden}
body{position:relative;font-family:"Source Sans 3","Myriad Pro",Arial,sans-serif;color:var(--text);background:var(--sand)}
.abs{position:absolute}

/* header */
.site-header{left:0;top:0;width:986px;height:64px;background:var(--ink)}
.brand{left:108px;top:12px;font-size:31px;font-weight:300;color:var(--white);letter-spacing:-0.3px}
.login{left:748px;top:20px;width:62px;height:23px;background:var(--pink);color:var(--white);font-size:13px;font-weight:600;text-align:center;line-height:23px}
.register{left:820px;top:23px;font-size:13px;color:var(--white);font-weight:600}

/* nav */
.main-nav{left:0;top:64px;width:986px;height:45px;background:var(--white)}
.main-nav ul{list-style:none;position:absolute;left:108px;top:0;display:flex;height:45px;border-left:1px solid var(--rule)}
.main-nav li{height:45px;line-height:44px;font-size:13px;color:var(--text);border-right:1px solid var(--rule);text-align:center}
.main-nav li.active{color:var(--pink)}
.cart{left:823px;top:0;width:56px;height:45px;border-left:1px solid var(--rule)}
.cart-count{position:absolute;left:30px;top:15px;width:15px;height:15px;background:var(--pink);color:var(--white);font-size:9px;font-weight:600;text-align:center;line-height:15px}

/* hero */
.hero{left:0;top:109px;width:986px;height:253px;background:var(--ink)}
.panel{position:absolute;top:0;height:253px;overflow:hidden}
.panel .photo{position:absolute;inset:0}
.panel .caption{position:absolute;left:0;right:0;bottom:0;height:68px;background:rgba(30,30,30,.72);padding:8px 0 0 16px;color:var(--white)}
.caption h2{font-size:25px;font-weight:400;line-height:30px}
.caption p{font-size:10.5px;color:#d8d8d8;margin-top:2px}
.collection-tag{position:absolute;right:26px;bottom:18px;width:126px;height:30px;background:var(--pink);color:var(--white);font-size:15px;text-align:center;line-height:30px}

/* shop bar */
.shop-bar{left:0;top:362px;width:986px;height:65px;background:var(--bar)}
.shop-label{left:148px;top:383px;font-size:17px;color:var(--white)}
.select{height:30px;top:380px;background:var(--field);color:var(--white);font-size:12.5px;line-height:30px;padding-left:13px}
.select svg{position:absolute;right:12px;top:12px}
.search-btn{left:384px;top:380px;width:74px;height:30px;background:#444;color:var(--white);font-size:14px;font-weight:600;text-align:center;line-height:30px}
.search-field{left:530px;top:380px;width:259px;height:30px;background:var(--field);color:#777;font-size:11.5px;font-style:italic;line-height:30px;padding-left:13px}
.go{left:789px;top:380px;width:49px;height:30px;background:var(--pink);color:var(--white);font-size:13px;font-weight:600;line-height:30px;padding-left:10px}

/* products */
.card{position:absolute;width:176px;height:135px;background:var(--white);box-shadow:0 1px 2px rgba(0,0,0,.12);padding:2px}
.card .photo{position:relative;width:172px;height:100px}
.card .label{position:absolute;left:0;bottom:0;width:103px;height:18px;background:rgba(40,40,40,.72);color:var(--white);font-size:12px;line-height:18px;padding-left:8px}
.card .price{position:absolute;left:16px;bottom:8px;font-size:13.5px;color:var(--text)}
.card .add{position:absolute;right:2px;bottom:2px;width:95px;height:27px;background:var(--pink);color:var(--white);font-size:12px;font-weight:600;text-align:center;line-height:27px}

/* sidebar */
.cat-head{left:706px;top:450px;width:173px;height:36px;background:var(--ink);color:var(--white);font-size:19px;line-height:36px;padding-left:14px}
.cat-list{left:706px;top:486px;width:173px;height:186px;background:var(--white);list-style:none;padding:17px 0 0 20px}
.cat-list li{font-size:12.5px;height:32.4px;color:var(--text);display:flex;align-items:flex-start;gap:14px}
.cat-list li::before{content:"";width:4px;height:4px;background:var(--pink);margin-top:7px;transform:rotate(45deg)}
.cat-list li.active{color:var(--pink);text-decoration:underline}
.promo{left:706px;width:173px;height:76px;text-align:center;color:var(--white)}
.promo .t{font-size:16px;font-weight:600;padding-top:11px;line-height:20px}
.promo .p{font-size:25px;font-weight:600;color:var(--yellow);line-height:28px}
.promo-pink{top:672px;background:linear-gradient(180deg,#e8577f 0%,#cf3d68 60%,#a92f4f 100%)}
.promo-blue{top:748px;background:linear-gradient(180deg,#6c9ae0 0%,#5b86cc 60%,#3f64a8 100%)}
.shipping{left:706px;top:824px;width:173px;height:75px;background:repeating-linear-gradient(135deg,var(--pink) 0 4px,var(--white) 4px 8px);padding:5px}
.shipping-inner{width:100%;height:100%;background:var(--white);position:relative}
.shipping .box{position:absolute;left:8px;top:10px;width:34px;height:36px;background:#c9a47a}
.shipping .t{position:absolute;left:54px;top:17px;font-size:15px;font-weight:600;color:var(--pink)}
.shipping .s{position:absolute;left:56px;top:37px;font-size:12px;color:var(--text)}

/* footer */
.site-footer{left:0;top:930px;width:986px;height:215px;background:var(--ink)}
.col h3{font-size:17px;font-weight:400;color:var(--pink);margin-bottom:13px}
.col ul{list-style:none}
.col li{font-size:11px;color:#d0d0d0;height:24.4px;display:flex;gap:9px}
.col li::before{content:"";width:3px;height:3px;background:var(--pink);margin-top:6px;transform:rotate(45deg)}
.news p{font-size:10.5px;color:#e0e0e0;line-height:16px;width:160px}
.email{width:157px;height:26px;background:#d6d6d6;color:#555;font-size:10.5px;line-height:26px;padding-left:10px;margin-top:12px}
.subscribe{width:95px;height:25px;background:var(--pink);color:var(--white);font-size:13px;font-weight:600;text-align:center;line-height:25px;margin-top:8px}
.social{display:flex;gap:10px}
.social span{width:21px;height:21px;background:#3a3a3a;color:var(--white);font-size:6.5px;text-align:center;line-height:21px}
.cards{display:flex;gap:13px}
.cards span{width:31px;height:19px;background:var(--white);color:var(--text);font-size:6.5px;font-weight:600;text-align:center;line-height:19px;border-radius:2px}
.copyright{left:0;top:1145px;width:986px;height:55px;background:var(--ink-deep);color:#ddd;font-size:10.5px;text-align:center;line-height:52px}
</style>
</head>
<body>

<header class="site-header abs">
  <div class="brand abs">studio nine harbors</div>
  <div class="login abs">Login</div>
  <div class="register abs">Or Register</div>
</header>

<nav class="main-nav abs">
  <ul>
    <li class="active" style="width:70px">Home</li>
    <li style="width:78px">Products</li>
    <li style="width:67px">About</li>
    <li style="width:55px">Page</li>
    <li style="width:62px">Blog</li>
    <li style="width:73px">Contact</li>
  </ul>
  <div class="cart abs">
    <svg class="abs" style="left:10px;top:18px" width="14" height="11" viewBox="0 0 14 11" fill="none" stroke="#333" stroke-width="1.1"><path d="M0 1h2.5l2 6h7l1.5-4.5H4"/><circle cx="5.5" cy="9.5" r="1"/><circle cx="10.5" cy="9.5" r="1"/></svg>
    <div class="cart-count">0</div>
  </div>
</nav>

<section class="hero abs">
  <div class="panel" style="left:0;width:137px">
    <div class="photo" role="img" aria-label="Pink bath brush with white bristles on a pink towel" style="background:linear-gradient(160deg,#f3d8e2 0%,#e7a3bd 35%,#dc5d8f 60%,#c23a6c 80%,#8a2a4a 100%)"></div>
    <div class="caption"><h2>Bathe</h2><p>Lorem Ipsum is simply..</p></div>
  </div>
  <div class="panel" style="left:139px;width:137px">
    <div class="photo" role="img" aria-label="Table setting with white plate, wine glass and woven placemat" style="background:linear-gradient(170deg,#5e4a3a 0%,#8d7a66 30%,#c9c3b8 55%,#e4e0d8 75%,#a89d8c 100%)"></div>
    <div class="caption"><h2>Dine</h2><p>Lorem Ipsum is simply..</p></div>
  </div>
  <div class="panel" style="left:278px;width:431px">
    <div class="photo" role="img" aria-label="Bright living room with a dark grey sofa, striped cushions, potted plant and grid patterned rug" style="background:linear-gradient(180deg,#cfcac4 0%,#e6e3de 22%,#b8b2aa 38%,#4a4a4e 52%,#2e2e31 66%,#7d7b79 78%,#a6a3a0 100%)"></div>
    <div class="caption" style="background:none;padding-left:24px"><h2>Rugs</h2><p>Lorem Ipsum is simply dummy.</p></div>
    <div class="collection-tag">2014 Collection</div>
  </div>
  <div class="panel" style="left:711px;width:136px">
    <div class="photo" role="img" aria-label="Woven decorative balls in a bowl before a leaf print cushion" style="background:linear-gradient(150deg,#6fa79c 0%,#4d7c74 30%,#5a3f3f 55%,#b9a78a 75%,#2d2424 100%)"></div>
    <div class="caption"><h2>Decorative</h2><p>Lorem Ipsum is simply..</p></div>
  </div>
  <div class="panel" style="left:849px;width:137px">
    <div class="photo" role="img" aria-label="Pale pink bedroom with bed and soft throw" style="background:linear-gradient(160deg,#b8aeb0 0%,#e9d9dc 35%,#dcb8c0 60%,#c79aa4 100%)"></div>
    <div class="caption"><h2>Sleep</h2><p>Lorem Ipsum is simply..</p></div>
  </div>
</section>

<section class="shop-bar abs"></section>
<div class="shop-label abs">Shop by:</div>
<div class="select abs" style="left:230px;width:137px">Categories<svg width="8" height="5" viewBox="0 0 8 5" fill="none" stroke="#aaa"><path d="M0.5 0.5 4 4 7.5 0.5"/></svg></div>
<div class="search-btn abs">Search</div>
<div class="select abs" style="left:458px;width:72px">All<svg width="8" height="5" viewBox="0 0 8 5" fill="none" stroke="#aaa"><path d="M0.5 0.5 4 4 7.5 0.5"/></svg></div>
<div class="search-field abs">Search for Products</div>
<div class="go abs">GO ›</div>

<main>
  <article class="card" style="left:108px;top:450px"><div class="photo" role="img" aria-label="Woven placemat with white plate and grapes on a wooden table" style="background:linear-gradient(160deg,#eeeae0 0%,#b89868 30%,#a5834f 60%,#d2a673 100%)"><div class="label">Lorem Ipsum is.</div></div><div class="price">$ 20.55</div><div class="add">+ Add to Cart</div></article>
  <article class="card" style="left:308px;top:450px"><div class="photo" role="img" aria-label="Round jute rug ringed with colourful felt circles" style="background:radial-gradient(circle at 50% 45%,#d8c3a0 0%,#c9a981 28%,#e36b6b 40%,#5c8bd0 50%,#4a2f2f 70%,#3a2424 100%)"><div class="label">Lorem Ipsum is.</div></div><div class="price">$ 20.55</div><div class="add">+ Add to Cart</div></article>
  <article class="card" style="left:508px;top:450px"><div class="photo" role="img" aria-label="Pink bath brush with pearl beads on a pink towel" style="background:linear-gradient(150deg,#f6e6ec 0%,#f1b7cc 35%,#e66a9a 65%,#d94a82 100%)"><div class="label">Lorem Ipsum is.</div></div><div class="price">$ 10.55</div><div class="add">+ Add to Cart</div></article>

  <article class="card" style="left:108px;top:608px"><div class="photo" role="img" aria-label="Dark grey sofa with striped cushions on a grid rug" style="background:linear-gradient(180deg,#dcd8d2 0%,#c8c3bc 25%,#3c3c40 45%,#2c2c2f 62%,#8a8886 80%,#a9a6a2 100%)"><div class="label">Lorem Ipsum is.</div></div><div class="price">$ 95.55</div><div class="add">+ Add to Cart</div></article>
  <article class="card" style="left:308px;top:608px"><div class="photo" role="img" aria-label="Carved wooden vase and woven balls in a bowl before a teal wall" style="background:linear-gradient(120deg,#4e3a30 0%,#7a5a48 30%,#7fb3a8 55%,#a89578 75%,#2e2a28 100%)"><div class="label">Lorem Ipsum is.</div></div><div class="price">$ 30.55</div><div class="add">+ Add to Cart</div></article>
  <article class="card" style="left:508px;top:608px"><div class="photo" role="img" aria-label="Multicoloured patchwork rug beside a blue chair" style="background:linear-gradient(180deg,#e9e7e3 0%,#cfd4da 30%,#e2456e 50%,#3e6fcf 65%,#f0b63c 80%,#c4325c 100%)"><div class="label">Lorem Ipsum is.</div></div><div class="price">$ 55.55</div><div class="add">+ Add to Cart</div></article>

  <article class="card" style="left:108px;top:765px"><div class="photo" role="img" aria-label="Rolled white towels stacked on a teal towel" style="background:linear-gradient(180deg,#5a3e2c 0%,#8a6a52 18%,#eeece7 40%,#e0ddd6 62%,#5fb0a2 80%,#3f8c80 100%)"><div class="label">Lorem Ipsum is.</div></div><div class="price">$ 15.55</div><div class="add">+ Add to Cart</div></article>
  <article class="card" style="left:308px;top:765px"><div class="photo" role="img" aria-label="White wall decoration framed by colourful felt ball garlands" style="background:linear-gradient(90deg,#cfc8c0 0%,#e8e6e2 35%,#f2f1ee 50%,#e5e2dd 65%,#c8c0b8 100%)"><div class="label">Lorem Ipsum is.</div></div><div class="price">$ 80.55</div><div class="add">+ Add to Cart</div></article>
  <article class="card" style="left:508px;top:765px"><div class="photo" role="img" aria-label="Cream textured table runner with plate on a wooden table" style="background:linear-gradient(150deg,#f0ece4 0%,#e3dccf 40%,#d6c9b3 60%,#c58a4e 80%,#a86a34 100%)"><div class="label">Lorem Ipsum is.</div></div><div class="price">$ 10.55</div><div class="add">+ Add to Cart</div></article>
</main>

<aside>
  <div class="cat-head abs">Categories</div>
  <ul class="cat-list abs">
    <li class="active">Rugs</li><li>Bathe</li><li>Dine</li><li>Decorative</li><li>Sleep</li>
  </ul>
  <div class="promo promo-pink abs" role="img" aria-label="Pink sofa collection promotion"><div class="t">2014 Collection</div><div class="p">$295.0</div></div>
  <div class="promo promo-blue abs" role="img" aria-label="Blue sofa collection promotion"><div class="t">Best Collection</div><div class="p">$256.0</div></div>
  <div class="shipping abs"><div class="shipping-inner">
    <div class="box" role="img" aria-label="Delivery trolley with parcel"></div>
    <div class="t">FREE Shipping</div><div class="s">On All Items</div>
  </div></div>
</aside>

<footer class="site-footer abs">
  <div class="col abs" style="left:108px;top:22px"><h3>Quick Menu</h3><ul><li>Home</li><li>About Us</li><li>Blog</li><li>Testimonials</li><li>Contact us</li></ul></div>
  <div class="col abs" style="left:236px;top:22px"><h3>Categories</h3><ul><li>Rugs</li><li>Bathe</li><li>Dine</li><li>Decorative</li><li>Sleep</li></ul></div>
  <div class="col abs" style="left:359px;top:22px"><h3>Your Account</h3><ul><li>Order Status</li><li>My Wishlist</li><li>Order History</li><li>Newsletter</li></ul></div>
  <div class="col news abs" style="left:505px;top:22px"><h3>Newsletter Sign Up</h3><p>Lorem ipsudolor sit ec adipiscing elitsite amet</p><div class="email">Email Address</div><div class="subscribe">Subscribe</div></div>
  <div class="col abs" style="left:707px;top:22px"><h3>Follow us</h3>
    <div class="social"><span>Folio</span><span>Chirp</span><span>Ringo</span><span>Workly</span></div>
    <h3 style="margin-top:22px">Newsletter Sign Up</h3>
    <div class="cards"><span>Payvale</span><span>Carda</span><span>Duocard</span><span>Farcard</span></div>
  </div>
</footer>
<div class="copyright abs">Copyright © 2014 studio nine harbors. All rights reserved.</div>

</body>
</html>
```